New Business Cards for Tormin Group

We need a new Business Card to compliment our new logo. We are a vibrant design, manufacture and install business providing recreation areas, public parks and Municipal spaces. We want business cards that are classy, modern and clean.

We have recently changed our logo, and are celebrating our 40th anniversary. We want business cards with a new modern design to reflect our status.

Target Market(s)

Customers

Contact Information for Business Card

We need all the details of our 3 offices as per the business card attached. Please disregard the old logo on the business card, the other three files show our new logo.

Requirements
Must have
• All info as per attached business card but with new logo.
Nice to have

```html
<!DOCTYPE html>
<html lang="en">
<head>
<meta charset="utf-8">
<title>Tormin Group – Business Card</title>
<link rel="stylesheet" href="https://fonts.googleapis.com/css2?family=Lato:wght@400;700&display=swap">
<style>
  :root {
    --page-bg: #e9e9ea;
    --card-bg: #ffffff;
    --brand-red: #e8303a;
    --ink-dark: #3d3d3f;
    --ink-body: #555557;
    --rule-grey: #d4d4d6;
    --band-dark: #4a4a4c;
    --white: #ffffff;
  }
  * { margin: 0; padding: 0; box-sizing: border-box; }
  html, body {
    width: 1200px; height: 1200px; overflow: hidden;
    background: var(--page-bg);
    font-family: "Lato", Arial, sans-serif;
  }
  .card {
    position: absolute; left: 176px; top: 314px;
    width: 848px; height: 492px;
    background: var(--card-bg);
    border-radius: 28px;
    overflow: hidden;
  }
  .person-name {
    position: absolute; left: 36px; top: 76px;
    font-size: 31px; font-weight: 400; color: var(--brand-red);
  }
  .person-role {
    position: absolute; left: 36px; top: 118px;
    font-size: 20px; color: var(--ink-dark);
  }
  .contact-line {
    position: absolute; left: 36px;
    font-size: 16px; color: var(--ink-dark);
  }
  .contact-line .label { color: var(--brand-red); }
  .contact-phone { top: 176px; }
  .contact-email { top: 208px; }

  .brand {
    position: absolute; left: 600px; top: 66px;
    display: flex; align-items: center; gap: 14px;
  }
  .brand-dot {
    width: 84px; height: 84px; border-radius: 50%;
    background: var(--brand-red);
  }
  .brand-name {
    font-size: 27px; font-weight: 700; color: var(--ink-dark);
    letter-spacing: 0.5px; line-height: 1.05;
  }

  .divider {
    position: absolute; left: 36px; top: 246px;
    width: 779px; height: 2px; background: var(--rule-grey);
  }
  .divider-accent {
    position: absolute; left: 0; top: -1px;
    width: 251px; height: 3px; background: var(--brand-red);
  }

  .office {
    position: absolute; top: 264px;
    font-size: 15.5px; color: var(--ink-body);
    line-height: 26px;
  }
  .office-title {
    font-size: 20px; color: var(--brand-red);
    margin-bottom: 2px; line-height: 30px;
  }
  .office-head { left: 36px; }
  .office-dubai { left: 331px; }
  .office-doha { left: 602px; top: 268px; }

  .footer-band {
    position: absolute; left: 0; bottom: 0;
    width: 100%; height: 65px; background: var(--band-dark);
  }
  .web-address {
    position: absolute; left: 213px; top: 427px;
    width: 417px; height: 57px;
    background: var(--brand-red);
    border: 3px solid var(--white); border-top: none;
    color: var(--white); font-size: 22px;
    display: flex; align-items: center; justify-content: center;
  }
</style>
</head>
<body>
  <main class="card">
    <h1 class="person-name">Rami Haddane</h1>
    <p class="person-role">Managing Partner</p>
    <p class="contact-line contact-phone"><span class="label">Phone:</span> +971 (0)50 318 4072</p>
    <p class="contact-line contact-email"><span class="label">Email:</span> rami@tormingroup.com</p>

    <div class="brand">
      <span class="brand-dot"></span>
      <span class="brand-name">TORMIN<br>GROUP</span>
    </div>

    <div class="divider"><span class="divider-accent"></span></div>

    <section class="office office-head">
      <h2 class="office-title">Head Office</h2>
      <p>P.O. Box: 41820 Abu Dhabi. U.A.E</p>
      <p>Tel No: +971 (0)2 4417350</p>
      <p>Fax No: +971(0)2 4417351</p>
      <p>Email: sales@tormingroup.com</p>
    </section>

    <section class="office office-dubai">
      <h2 class="office-title">Dubai Office</h2>
      <p>P.O. Box: 208734 Dubai, U.A.E</p>
      <p>Tel No: +971 (0)4 382516</p>
      <p>Fax No: +971(0)4 382597</p>
      <p>Email: sales@tormingroup.com</p>
    </section>

    <section class="office office-doha">
      <h2 class="office-title">Qater Office</h2>
      <p>P.O. Box: 17392 Doha, Qatter</p>
      <p>Tel No: +974 44731068</p>
      <p>Fax No: +971 44520937</p>
      <p>Email: sales@tormingroup.com</p>
    </section>

    <div class="footer-band"></div>
    <div class="web-address">www.tormingroup.com</div>
  </main>
</body>
</html>
```